Business Card Design

I am an Event and Wedding Planner in need of an eye catching business card featuring my logo (attached), my contact details, and my company tagline (Making every celebration glow with wonder...) I would like the tagline in font similar the logo's font.
Updates
I have just noticed that my logo has a misspelling so for the final design, I will be uploading a corrected logo as soon as I have it.
My apologies.
Reason: Waiting on a corrected logo...Lantern is misspelled and it should say Weddings not Wedding
The logo has been corrected so now Lantern is spelled correctly and it says Weddings instead of Wedding. Please use Edwardian Script ITC as the font for the tagline so it will match the logo. Thank you for your patience.
Target Market(s)
Engaged couples and people hosting milestone celebrations. 25-50 years old, predominately female
Industry/Entity Type
Business
Contact Information for Business Card
Rosalind Merrow, Event Manager / Owner, Mobile: 0491 868 254, Email: rosalind@velvetlanternco.com.au, www.velvetlanternco.com.au, Making every celebration glow with wonder...

```html
<!DOCTYPE html>
<html lang="en">
<head>
<meta charset="utf-8">
<title>Velvet Lantern – Business Card</title>
<link href="https://fonts.googleapis.com/css2?family=Italianno&family=Pinyon+Script&family=Cormorant+Garamond:wght@400;500&display=swap" rel="stylesheet">
<style>
  :root {
    --backdrop: #efefef;
    --card: #fbfbfa;
    --ink: #2b2b2b;
    --ink-soft: #4a4a4a;
    --coral: #e0443a;
    --edge: #e8696a;
    --blush: #ecd3c9;
    --charcoal: #3a3a3c;
    --dot: #555;
  }
  * { box-sizing: border-box; margin: 0; padding: 0; }
  html, body { width: 1200px; height: 1000px; overflow: hidden; }
  body { background: var(--backdrop); position: relative; font-family: "Cormorant Garamond", Georgia, serif; color: var(--ink); }

  .card {
    position: absolute;
    width: 520px;
    height: 300px;
    background: var(--card);
    border-bottom: 6px solid var(--edge);
    box-shadow: 0 10px 24px rgba(0,0,0,0.12);
    overflow: hidden;
  }
  .card__frame {
    position: absolute;
    inset: 14px;
    border: 2px dotted var(--dot);
    border-radius: 1px;
    opacity: .75;
  }

  /* Back of card */
  .card--back { left: 600px; top: 130px; }
  .brand-mark {
    position: absolute;
    left: 50%; top: 70px;
    transform: translateX(-50%);
    display: flex; flex-direction: column; align-items: center; gap: 8px;
  }
  .brand-mark__circle { width: 76px; height: 76px; border-radius: 50%; background: var(--charcoal); }
  .brand-mark__name { font-size: 17px; font-weight: 500; letter-spacing: .04em; color: var(--ink); }
  .tagline {
    position: absolute;
    left: 30px; right: 30px; top: 192px;
    text-align: center;
    font-family: "Pinyon Script", cursive;
    font-size: 25px;
    line-height: 1.3;
    color: var(--coral);
  }

  /* Front of card */
  .card--front { left: 110px; top: 560px; }
  .heart-decor { position: absolute; left: 20px; top: -10px; width: 170px; height: 130px; }
  .logo {
    position: absolute;
    left: 46px; top: 44px;
    display: flex; flex-direction: column; gap: 2px;
  }
  .logo__name { font-size: 19px; font-weight: 500; color: var(--ink); line-height: 1; }
  .logo__sub { font-size: 12px; color: var(--ink-soft); }
  .person {
    position: absolute;
    right: 44px; top: 128px;
    width: 290px;
  }
  .person__name {
    font-family: "Italianno", cursive;
    font-size: 52px;
    font-weight: 400;
    line-height: .95;
    color: var(--ink);
    text-align: right;
    white-space: nowrap;
  }
  .person__role { font-size: 18px; line-height: 1.2; margin: 4px 0 6px 24px; color: var(--ink); }
  .contact { list-style: none; margin-left: 24px; }
  .contact li { display: flex; align-items: center; gap: 6px; font-size: 12px; line-height: 1.35; color: var(--ink-soft); white-space: nowrap; }
  .contact svg { width: 8px; height: 8px; flex: none; }
</style>
</head>
<body>

  <section class="card card--back" aria-label="Business card back">
    <div class="card__frame"></div>
    <div class="brand-mark">
      <div class="brand-mark__circle"></div>
      <div class="brand-mark__name">Velvet Lantern</div>
    </div>
    <p class="tagline">Making every celebration glow with wonder...</p>
  </section>

  <section class="card card--front" aria-label="Business card front">
    <div class="card__frame"></div>
    <svg class="heart-decor" role="img" aria-label="Faint blush heart ornament" viewBox="0 0 170 130">
      <defs>
        <linearGradient id="blushFade" x1="0" y1="0" x2="0" y2="1">
          <stop offset="0" stop-color="#ecd3c9" stop-opacity=".85"/>
          <stop offset="1" stop-color="#ecd3c9" stop-opacity=".45"/>
        </linearGradient>
      </defs>
      <rect x="0" y="0" width="170" height="130" rx="10" fill="url(#blushFade)" opacity=".55"/>
    </svg>
    <div class="logo">
      <span class="logo__name">Velvet Lantern</span>
      <span class="logo__sub">Weddings and Events</span>
    </div>
    <div class="person">
      <h1 class="person__name">Rosalind Merrow</h1>
      <p class="person__role">Event Manager / Owner</p>
      <ul class="contact">
        <li><svg viewBox="0 0 10 10"><path d="M2 1 L4 1 L4.6 3 L3.4 3.8 Q4.4 5.8 6.2 6.6 L7 5.4 L9 6 L9 8 Q5 9 1 3 Z" fill="var(--coral)"/></svg>0491 868 254</li>
        <li><svg viewBox="0 0 10 10"><rect x="0.5" y="2" width="9" height="6" rx="1" fill="var(--coral)"/><path d="M0.8 2.3 L5 5.5 L9.2 2.3" stroke="#fff" stroke-width="0.8" fill="none"/></svg>rosalind@velvetlanternco.com.au</li>
        <li><svg viewBox="0 0 10 10"><circle cx="5" cy="5" r="4.5" fill="var(--coral)"/><circle cx="5" cy="5" r="1.6" fill="#fff"/></svg>www.velvetlanternco.com.au</li>
      </ul>
    </div>
  </section>

</body>
</html>
```